New business card/stationary for a consulting company

I am looking for a clean and very professional looking business card for my consulting company as well as corresponding stationary. I am uploading our logo. I like simple and powerful for the feel. No graphics but I am open on everything else. Below is my contact information but would like the final to be in a version I can add my employees information into and print. Thank you.

Daniel Whitcombe
dan@ferncliffadvisory.com
2870 North 9th Avenue, Summit Floor, Elm Ridge, Illinois 60531
www.ferncliffadvisory.com

Industry/Entity Type

Consulting

Contact Information for Business Card

Daniel Whitcombe
dan@ferncliffadvisory.com
www.ferncliffadvisory.com

Font styles to use
Serif
Sans Serif

Requirements
Must have
• Our logo and the business card details.
Nice to have
• our website www.ferncliffadvisory.com

```html
<!DOCTYPE html>
<html lang="en">
<head>
<meta charset="utf-8">
<title>Ferncliff Advisory – Business Card</title>
<link href="https://fonts.googleapis.com/css2?family=Questrial&family=Open+Sans:wght@400;700&display=swap" rel="stylesheet">
<style>
  :root {
    --navy: #0f0c7c;
    --white: #ffffff;
    --paper: #fbfbfb;
    --ink-grey: #6b6b6b;
    --backdrop: #2a2a2a;
  }
  * { margin: 0; padding: 0; box-sizing: border-box; }
  html, body { width: 1200px; height: 900px; overflow: hidden; }
  body {
    background: var(--backdrop);
    position: relative;
    font-family: "Open Sans", sans-serif;
  }
  .card {
    position: absolute;
    left: 285px;
    width: 630px;
    height: 360px;
    overflow: hidden;
    box-shadow: 0 10px 30px rgba(0,0,0,0.45);
  }
  .card-front { top: 70px; background: var(--paper); }
  .card-back { top: 470px; background: var(--paper); }

  .wordmark {
    position: absolute;
    display: flex;
    align-items: center;
    gap: 14px;
    font-family: "Questrial", sans-serif;
    font-size: 30px;
    letter-spacing: 1px;
    white-space: nowrap;
  }
  .wordmark-mark { width: 22px; height: 22px; }
  .card-front .wordmark {
    left: 50%; top: 50%;
    transform: translate(-50%, -50%);
    color: var(--navy);
  }
  .card-front .wordmark-mark { background: var(--navy); }

  .back-panel {
    position: absolute;
    left: 0; top: 0;
    width: 330px; height: 100%;
    background: linear-gradient(135deg, #14119a 0%, var(--navy) 55%, #0a0866 100%);
  }
  .back-panel .wordmark {
    left: 50%; top: 50%;
    transform: translate(-50%, -50%);
    color: var(--white);
    font-size: 24px;
    gap: 10px;
  }
  .back-panel .wordmark-mark { width: 18px; height: 18px; background: var(--white); }

  .edge-stripe {
    position: absolute;
    right: 0; top: 0;
    width: 14px; height: 100%;
    background: var(--navy);
  }

  .contact {
    position: absolute;
    left: 368px;
    top: 100px;
    color: var(--ink-grey);
  }
  .contact-name {
    color: var(--navy);
    font-weight: 700;
    font-size: 19px;
    letter-spacing: 0.3px;
    margin-bottom: 10px;
  }
  .contact-address {
    font-size: 14px;
    line-height: 19px;
    margin-bottom: 6px;
  }
  .contact-line {
    display: flex;
    align-items: center;
    gap: 9px;
    font-size: 14px;
    line-height: 21px;
  }
  .contact-line svg { width: 12px; height: 12px; flex: none; }
</style>
</head>
<body>

  <section class="card card-front" aria-label="Card front">
    <div class="wordmark">
      <span class="wordmark-mark"></span>
      <span class="wordmark-name">FERNCLIFF ADVISORY</span>
    </div>
  </section>

  <section class="card card-back" aria-label="Card back">
    <div class="back-panel">
      <div class="wordmark">
        <span class="wordmark-mark"></span>
        <span class="wordmark-name">FERNCLIFF ADVISORY</span>
      </div>
    </div>

    <div class="contact">
      <p class="contact-name">DANIEL WHITCOMBE</p>
      <p class="contact-address">2870 North 9th Avenue<br>Summit Floor, Elm Ridge<br>Illinois 60531</p>
      <p class="contact-line">
        <svg viewBox="0 0 12 12" aria-hidden="true"><rect x="0.5" y="2" width="11" height="8" fill="#0f0c7c"/><path d="M0.5 2 L6 6.5 L11.5 2" stroke="#fff" stroke-width="1" fill="none"/></svg>
        dan@ferncliffadvisory.com
      </p>
      <p class="contact-line">
        <svg viewBox="0 0 12 12" aria-hidden="true"><circle cx="6" cy="6" r="5.5" fill="#0f0c7c"/><path d="M3.5 6 H8.5 M6 3.5 V8.5" stroke="#fff" stroke-width="1"/></svg>
        www.ferncliffadvisory.com
      </p>
    </div>

    <div class="edge-stripe"></div>
  </section>

</body>
</html>
```